Design website for new email startup

We are starting a company called Pingo.QZ (it will live at http://pingo.qz).

We would like the main landing page for our site designed. We have provided a very simple wireframe to help provide direction for the content it should include, but we do not expect the designers to adhere to it at all - we encourage unique ideas. There is some sample text in the wireframe - this does not have to be used, but may provide ideas.

We provide an easy way for people to manage email for a custom domain name. For example if you own "yourhouseword.example" you can point your DNS records to us and we'll make it easy to have emails addressed to your domain get forwarded to your existing email (gmail, etc). Folks running blogs, and other small sites can quickly setup email addresses for their domains and manage them in one place.

(For technical folks, we have you point your dns mx records to us, hence the name. That way all your email hits us and we can redirect it wherever you want. We make it easy to manage a single domain or a bunch of domains. Many domain registrars offer this service for a fee, and have clumsy management tools. We provide a robust simple toolset for free, as well as premium options).

The goal of the landing page is to get folks into the signup flow. The second priority flow is to have them take a look at the premium plan offerings.

We may offer the winning designer additional work for the remainder of the site design.
Updates

I've changed this project to a committed payment.  It is no longer refundable.  Thank you.

Target Market(s)

Bloggers, podcasters, designers, app developers - people who are a little tech savvy.

Industry/Entity Type

It Company

Font styles to use
Sans Serif

Colors

Designer to choose colors to be used in the design.

Requirements
Must have
• A full fidelity mockup (comp) of the landing page including the source file (psd, ai, etc).

Some sort of logo treatment for the pingo.qz brand

A call to action for signup, such as the suggested 'Get Started Here'
Nice to have
• A hip startup feel

Incorporation of the email theme

Give the impression it is simple, easy and fast

```html
<!DOCTYPE html>
<html lang="en">
<head>
<meta charset="utf-8">
<title>Pingo.qz – Email for your domain</title>
<link rel="stylesheet" href="https://fonts.googleapis.com/css2?family=Open+Sans:wght@300;400;600&family=Neuton:wght@400&display=swap">
<style>
  :root {
    --bar: #333333;
    --accent: #d4502d;
    --red: #c9261a;
    --red-deep: #a82314;
    --hero-top: #d05535;
    --text-dark: #2e2e2e;
    --text-mid: #666666;
    --text-soft: #7a7a7a;
    --panel-bg: #f1f1f1;
    --white: #ffffff;
    --cta-top: #f7a21b;
    --cta-bottom: #e07a06;
    --tick: #7a1a10;
  }
  * { box-sizing: border-box; margin: 0; padding: 0; }
  html, body { width: 1200px; height: 1157px; overflow: hidden; }
  body { font-family: "Open Sans", sans-serif; color: var(--text-dark); background: var(--white); position: relative; }

  .topbar { position: absolute; top: 0; left: 0; width: 1200px; height: 45px; background: var(--bar); border-bottom: 4px solid var(--accent); }
  .social { position: absolute; left: 112px; top: 10px; display: flex; gap: 13px; }
  .social span { width: 20px; height: 20px; border-radius: 50%; background: #d8d8d8; display: block; }
  .nav { position: absolute; right: 103px; top: 0; display: flex; height: 41px; align-items: center; font-size: 14px; color: var(--white); }
  .nav a { color: var(--white); text-decoration: none; padding: 0 8px; height: 41px; line-height: 41px; }
  .nav a.current { background: var(--accent); }
  .nav .sep { padding: 0 8px 0 12px; }

  .header { position: absolute; top: 45px; left: 0; width: 1200px; height: 84px; }
  .brand { position: absolute; left: 110px; top: 18px; }
  .brand-name { font-size: 29px; font-weight: 400; color: var(--text-dark); line-height: 28px; letter-spacing: -0.5px; }
  .brand-tagline { font-size: 14px; color: var(--text-dark); line-height: 16px; }
  .callus { position: absolute; right: 110px; top: 35px; font-size: 14px; color: var(--text-mid); }
  .callus .phone { color: var(--red); margin-left: 16px; }

  .hero { position: absolute; top: 129px; left: 0; width: 1200px; height: 394px; background: linear-gradient(var(--hero-top), var(--red-deep)); }
  .hero-foot { position: absolute; top: 523px; left: 0; width: 1200px; height: 62px; background: var(--panel-bg); }
  .hero-title { position: absolute; left: 112px; top: 175px; font-size: 45px; line-height: 60px; font-weight: 400; color: var(--white); letter-spacing: -0.3px; }
  .hero-title b { font-weight: 600; }
  .hero-lead { position: absolute; left: 115px; top: 245px; width: 410px; font-size: 14px; line-height: 20px; color: var(--white); }
  .ticks { position: absolute; left: 115px; top: 326px; list-style: none; color: var(--white); font-size: 14px; }
  .ticks li { display: flex; align-items: center; height: 32.5px; }
  .ticks svg { width: 24px; height: 24px; margin-right: 11px; }

  .cta { position: absolute; left: 113px; top: 496px; width: 357px; height: 53px; border-radius: 27px; background: linear-gradient(var(--cta-top), var(--cta-bottom)); box-shadow: 0 2px 4px rgba(0,0,0,.3); border: 2px solid #fbd08a; font-size: 16px; font-weight: 600; color: var(--white); }
  .cta span { position: absolute; top: 0; line-height: 49px; }
  .cta .go { left: 11px; }
  .cta .or { left: 163px; top: 10px; width: 29px; height: 29px; line-height: 29px; border-radius: 50%; background: #e48a0a; text-align: center; }
  .cta .plans { left: 204px; }

  .tablet { position: absolute; left: 642px; top: 206px; width: 447px; height: 345px; border-radius: 12px; background: linear-gradient(135deg, #3a3a3a 0%, #050505 40%, #000 100%); border: 2px solid #222; }
  .screen { position: absolute; left: 37px; top: 30px; width: 370px; height: 277px; background: radial-gradient(circle at 30% 40%, #4d7fd0 0%, #d8e3f1 35%, #ffffff 60%), #fff; }
  .cam { position: absolute; right: 10px; top: 165px; width: 12px; height: 12px; border-radius: 50%; background: #1a1a1a; border: 1px solid #333; }

  .strap { position: absolute; top: 585px; left: 0; width: 1200px; height: 123px; text-align: center; }
  .strap h2 { font-family: "Neuton", serif; font-weight: 400; font-size: 35px; color: var(--red); letter-spacing: 2.3px; margin-top: 24px; line-height: 42px; padding-left: 40px; }
  .strap p { font-size: 25px; color: var(--text-soft); letter-spacing: 1px; margin-top: 2px; padding-left: 72px; }

  .features { position: absolute; top: 708px; left: 0; width: 1200px; height: 398px; background: var(--panel-bg); }
  .feature { position: absolute; top: 0; width: 482px; height: 398px; }
  .feature h3 { text-align: center; font-size: 22px; font-weight: 600; color: var(--text-dark); margin-top: 42px; line-height: 30px; }
  .box { position: absolute; top: 130px; left: 0; width: 482px; height: 194px; background: var(--white); border: 2px solid #cfcfcf; padding: 52px 14px 0; text-align: center; font-size: 14px; line-height: 22px; font-weight: 300; color: var(--text-mid); }
  .icon { position: absolute; top: 92px; left: 203px; width: 76px; height: 76px; border-radius: 50%; background: var(--white); border: 2px solid #cfcfcf; display: flex; align-items: center; justify-content: center; }
  .more { position: absolute; top: 303px; left: 157px; width: 142px; height: 46px; border-radius: 10px; background: linear-gradient(#d8472c, #a9200f); border: 2px solid #f1f1f1; box-shadow: 0 2px 4px rgba(0,0,0,.35); color: var(--white); font-size: 20px; letter-spacing: .8px; display: flex; align-items: center; justify-content: center; }
  .feature-left { left: 108px; }
  .feature-right { left: 610px; }

  .footer { position: absolute; top: 1106px; left: 0; width: 1200px; height: 51px; background: var(--bar); color: var(--white); font-size: 13px; text-align: center; line-height: 49px; font-weight: 300; }
</style>
</head>
<body>
  <div class="topbar">
    <div class="social" aria-label="Social links"><span></span><span></span><span></span><span></span></div>
    <nav class="nav">
      <a class="current" href="#">How it works</a><span class="sep">|</span>
      <a href="#">Support</a><span class="sep">|</span>
      <a href="#">Login</a>
    </nav>
  </div>

  <header class="header">
    <div class="brand">
      <div class="brand-name">Pingo.qz</div>
      <div class="brand-tagline">For your our domain</div>
    </div>
    <div class="callus">Call us! <span class="phone">555-010-24680</span></div>
  </header>

  <section class="hero"></section>
  <div class="hero-foot"></div>
  <h1 class="hero-title">Sell Us Your <b>Domains</b></h1>
  <p class="hero-lead">Lorem ipsum dolor sit amet, consectetuer adipiscing elit, sed diam nonummy nibh euismod tincidunt ut laoreet dolore magna aliquam erat volutpat...</p>
  <ul class="ticks">
    <li><svg viewBox="0 0 24 24"><circle cx="12" cy="12" r="12" fill="var(--tick)"/><path d="M6 12.5l4 4 8-8" fill="none" stroke="#fff" stroke-width="3"/></svg>We make email easy</li>
    <li><svg viewBox="0 0 24 24"><circle cx="12" cy="12" r="12" fill="var(--tick)"/><path d="M6 12.5l4 4 8-8" fill="none" stroke="#fff" stroke-width="3"/></svg>Give us five minutes and we’ll get you email from your domain</li>
    <li><svg viewBox="0 0 24 24"><circle cx="12" cy="12" r="12" fill="var(--tick)"/><path d="M6 12.5l4 4 8-8" fill="none" stroke="#fff" stroke-width="3"/></svg>You take the mail we’ll keep the spam</li>
  </ul>
  <div class="cta"><span class="go">GET STARTED FREE</span><span class="or">OR</span><span class="plans">COMPARE PLANS</span></div>

  <div class="tablet">
    <div class="screen" role="img" aria-label="Illustration of a figure with a magnifying glass beside a globe and a web address"></div>
    <div class="cam"></div>
  </div>

  <section class="strap">
    <h2>Easily forward mail from your custom domain name</h2>
    <p>Whereever you want it</p>
  </section>

  <section class="features">
    <div class="feature feature-left">
      <h3>SkyRelay DNS to use pingo.qz</h3>
      <div class="box">Lorem ipsum dolor sit amet, consectetur adipisicingeiusmod tempor incididunt ut elit, sed do eiusmod tempor incididunt ut labore et dolore magna aliqua ut enim ad minim veniam eiusmod tempor incididunt utexercitation ullamco...</div>
      <div class="icon"><svg width="48" height="34" viewBox="0 0 48 34"><rect x="2" y="3" width="42" height="18" rx="2" fill="none" stroke="#333" stroke-width="3"/><text x="7" y="16" font-family="Open Sans, sans-serif" font-size="10" fill="#333">www.|</text><path d="M27 17l0 14 4-4 3 6 3-1-3-6 5 0z" fill="#333"/></svg></div>
      <div class="more">Read more</div>
    </div>
    <div class="feature feature-right">
      <h3>Namebarn Domain Registration</h3>
      <div class="box">Lorem ipsum dolor sit amet, consectetur adipisicingeiusmod tempor incididunt ut elit, sed do eiusmod tempor incididunt ut labore et dolore magna aliqua ut enim ad minim veniam eiusmod tempor incididunt utexercitation ullamco...</div>
      <div class="icon"><svg width="44" height="44" viewBox="0 0 44 44"><circle cx="22" cy="22" r="13" fill="none" stroke="#333" stroke-width="3"/><ellipse cx="22" cy="22" rx="6" ry="13" fill="none" stroke="#333" stroke-width="2"/><line x1="9" y1="22" x2="35" y2="22" stroke="#333" stroke-width="2"/><ellipse cx="22" cy="22" rx="21" ry="7" transform="rotate(40 22 22)" fill="none" stroke="#333" stroke-width="2.5"/></svg></div>
      <div class="more">Read more</div>
    </div>
  </section>

  <footer class="footer">© 2014 Pingo.qz, Inc. All rights reserved</footer>
</body>
</html>
```